Business Card for Professional Photographer

I'm looking for an eye catching modern clean design that compliments my logo/ website fonts & colours.
I specialise in architecture, corporate & commercial photography so I'm marketing to professional clients rather than portrait / wedding clients.

I would prefer to not have a solid black design.

My logo brand guide is as follows :

Main front font. : Reislust
Main font colour : #fff
Slogan front font : Ubuntu Bold
Monogram front font : Venti Medium
Container colour : #fff

I need print ready files in pdf .png & .eps formats.

Included in the files below are some screen grabs as reference to font & colours etc.

```html
<!DOCTYPE html>
<html lang="en">
<head>
<meta charset="utf-8">
<title>Northlight Studio – Business Card</title>
<link rel="stylesheet" href="https://fonts.googleapis.com/css2?family=Lato:wght@400;700;900&display=swap">
<style>
  :root {
    --backdrop: #3a3a3c;
    --gold-deep: #b8883e;
    --gold-mid: #d4b062;
    --gold-light: #f8eea6;
    --gold-text: #c49a52;
    --ink: #1d1d1d;
    --paper: #f4f4f4;
    --rule: #c9c9c9;
  }
  * { box-sizing: border-box; margin: 0; padding: 0; }
  html, body { width: 1200px; height: 1015px; overflow: hidden; }
  body {
    background: var(--backdrop);
    display: flex;
    flex-direction: column;
    align-items: center;
    justify-content: center;
    gap: 60px;
    font-family: "Lato", sans-serif;
  }
  .card {
    width: 620px;
    height: 354px;
    position: relative;
    overflow: hidden;
    box-shadow: 0 14px 30px rgba(0,0,0,.45);
  }

  /* Front */
  .card-front {
    background:
      radial-gradient(ellipse 55% 70% at 48% 42%, var(--gold-light) 0%, rgba(248,238,166,0) 70%),
      linear-gradient(120deg, var(--gold-mid) 0%, #e4cb7c 40%, var(--gold-mid) 70%, var(--gold-deep) 100%);
  }
  .front-brand {
    position: absolute;
    left: 0; right: 0; top: 148px;
    text-align: center;
  }
  .brand-name {
    font-family: "Lato", sans-serif;
    font-weight: 700;
  }
  .front-brand .brand-name { font-size: 38px; color: var(--ink); }
  .brand-tagline {
    font-family: "Lato", sans-serif;
    font-weight: 400;
  }
  .front-brand .brand-tagline { font-size: 14px; color: var(--ink); margin-top: 4px; }

  /* Back */
  .card-back { background: var(--paper); }
  .back-band {
    position: absolute;
    left: 0; right: 0; bottom: 0;
    height: 11px;
    background: linear-gradient(90deg, var(--gold-deep), var(--gold-light) 50%, var(--gold-deep));
  }
  .back-logo {
    position: absolute;
    left: 40px; top: 166px;
    display: flex;
    align-items: center;
    gap: 12px;
  }
  .logo-square {
    width: 30px; height: 30px;
    background: var(--gold-text);
    flex: none;
  }
  .back-logo .brand-name { font-size: 22px; line-height: 1.1; color: var(--gold-text); }
  .back-logo .brand-tagline { font-size: 11px; color: var(--gold-text); margin-top: 2px; }
  .divider {
    position: absolute;
    left: 372px; top: 0; bottom: 11px;
    width: 1px;
    background: var(--rule);
  }
  .contact {
    position: absolute;
    left: 396px; top: 70px;
    color: var(--ink);
    font-size: 15px;
    line-height: 1.3;
  }
  .contact-name {
    font-weight: 900;
    font-size: 20px;
    color: var(--gold-text);
    text-transform: uppercase;
  }
  .contact-role { font-size: 15px; margin-bottom: 4px; }
  .contact-row { display: flex; align-items: center; gap: 6px; font-size: 15px; }
  .contact-row svg { width: 13px; height: 13px; flex: none; fill: var(--gold-text); }
  .contact-address { font-size: 15px; margin-top: 4px; }
</style>
</head>
<body>

  <section class="card card-front" aria-label="Card front">
    <div class="front-brand">
      <p class="brand-name">Northlight Studio</p>
      <p class="brand-tagline">Spaces, Offices &amp; Brands</p>
    </div>
  </section>

  <section class="card card-back" aria-label="Card back">
    <div class="back-logo">
      <span class="logo-square"></span>
      <div>
        <p class="brand-name">Northlight Studio</p>
        <p class="brand-tagline">Spaces, Offices &amp; Brands</p>
      </div>
    </div>

    <div class="divider"></div>

    <div class="contact">
      <p class="contact-name">Daniel Hartley</p>
      <p class="contact-role">Managing Director</p>
      <p class="contact-row">
        <svg viewBox="0 0 16 16" aria-hidden="true"><path d="M3 1h3l1.5 4-2 1.3a9 9 0 0 0 4.2 4.2L11 8.5l4 1.5v3a2 2 0 0 1-2 2A12 12 0 0 1 1 3a2 2 0 0 1 2-2z"/></svg>
        044-987 654 321
      </p>
      <p class="contact-row">
        <svg viewBox="0 0 16 16" aria-hidden="true"><path d="M1 3h14v10H1z M2 4l6 5 6-5" stroke="#f4f4f4" stroke-width="1.2"/></svg>
        hello@northlightstudio.com
      </p>
      <p class="contact-row">
        <svg viewBox="0 0 16 16" aria-hidden="true"><circle cx="8" cy="8" r="7"/><path d="M1 8h14M8 1c3 3 3 11 0 14M8 1c-3 3-3 11 0 14" stroke="#f4f4f4" stroke-width="1" fill="none"/></svg>
        www.northlightstudio.com
      </p>
      <p class="contact-address">18 Harbour Lane<br>Westbury, 40217</p>
    </div>

    <div class="back-band"></div>
  </section>

</body>
</html>
```